I need a SEO-friendly Wordpress website (making sure to style H1, H2, H3, etc correctly) for a Hawaii-based law firm called Meridian Crest Legal Group. Comparable websites include https://brvlaw.example/ and https://www.lomrit.example/ for design reference. The current copy on the TarnAdvocate.example website can be used.

```html
<!DOCTYPE html>
<html lang="en">
<head>
<meta charset="utf-8">
<title>Meridian Crest Legal Group – Personal Injury, Family &amp; Divorce, Child Custody</title>
<link href="https://fonts.googleapis.com/css2?family=Oswald:wght@500;600;700&family=Lato:wght@400;700&display=swap" rel="stylesheet">
<style>
:root{
  --brand:#8b3508;
  --brand-light:#a5480f;
  --accent:#bb6310;
  --ink:#111111;
  --text:#555555;
  --panel:#f1f1f1;
  --line:#d5d5d5;
  --map:#8d9197;
  --white:#ffffff;
}
*{margin:0;padding:0;box-sizing:border-box}
html,body{width:1200px;height:3589px;overflow:hidden}
body{position:relative;background:var(--white);font-family:"Lato",sans-serif;color:var(--text)}
.abs{position:absolute}
h1,h2,h3{font-family:"Oswald",sans-serif;color:var(--ink);font-weight:600}
.btn{position:absolute;display:flex;align-items:center;justify-content:center;background:var(--accent);color:var(--white);font-family:"Oswald",sans-serif;font-weight:500;border-radius:3px;text-decoration:none}
.rule{position:absolute;height:3px;background:var(--brand)}
.photo{position:absolute}

/* top bar */
.topbar{left:0;top:0;width:1200px;height:52px;background:var(--brand)}
.brand-name{left:163px;top:12px;font-family:"Lato",sans-serif;font-weight:700;font-size:22px;color:var(--white)}
.call-label{left:793px;top:17px;font-size:13px;color:#f2d9c8}
.call-icon{left:867px;top:11px;width:29px;height:29px;background:var(--accent);border-radius:3px;display:flex;align-items:center;justify-content:center}
.call-number{left:911px;top:14px;font-size:17px;color:var(--white)}

/* nav */
.nav{left:0;top:52px;width:1200px;height:45px;background:var(--white)}
.nav ul{list-style:none;display:flex;position:absolute;left:163px;top:15px;gap:0}
.nav li{font-size:12px;color:#222;margin-right:24px}
.nav li.active{color:var(--brand-light)}
.search{left:1000px;top:65px}

/* hero */
.hero-bg{left:0;top:97px}
.hero-tag{left:162px;top:181px;width:404px;height:43px;background:var(--brand-light);color:#fbe9dc;font-size:12.5px;display:flex;align-items:center;padding-left:10px}
.hero h1{position:absolute;left:163px;top:240px;font-size:66px;line-height:68px;color:var(--white);font-weight:700}
.hero .btn{left:162px;top:503px;width:134px;height:48px;font-size:19px}
.hero-photo-a{left:638px;top:173px;width:562px;height:373px;border-radius:10px 0 10px 10px;background:linear-gradient(135deg,#5a2613,#8a4a2a 45%,#2c1c16)}
.hero-photo-b{left:750px;top:404px;width:337px;height:375px;border-radius:10px;background:linear-gradient(160deg,#c89a7c,#a06a4e 50%,#3c2016)}

/* welcome */
.welcome-photo{left:162px;top:853px;width:315px;height:438px;background:linear-gradient(180deg,#b8a58e,#6b5a4a 55%,#3a2a20)}
.welcome h2{position:absolute;left:507px;top:878px;width:520px;font-size:41px;line-height:46px}
.welcome .rule{left:514px;top:979px;width:70px}
.welcome p{position:absolute;left:507px;width:525px;font-size:11.5px;line-height:19.5px}
.welcome .btn{left:507px;top:1220px;width:90px;height:37px;font-size:13px}

/* section titles */
.section-title{position:absolute;left:0;width:1200px;text-align:center;font-size:40px}

/* practice cards */
.card{position:absolute;top:1489px;width:203px;height:234px;background:var(--white);box-shadow:0 0 8px rgba(0,0,0,.14);padding:0 13px}
.card svg{position:absolute;left:13px;top:24px}
.card h3{position:absolute;left:13px;top:91px;font-size:17px;font-weight:500}
.card p{position:absolute;left:13px;top:121px;width:180px;font-size:11px;line-height:19.5px}
.card .more{position:absolute;left:13px;top:194px;font-family:"Oswald",sans-serif;font-size:12px;color:var(--accent);display:flex;align-items:center;gap:4px}

/* attorneys */
.attorneys-band{left:0;top:1845px;width:1200px;height:413px;background:var(--brand)}
.attorney-photo{left:709px;top:1786px;width:329px;height:419px;background:linear-gradient(170deg,#8a7a66,#4a4038 45%,#1d1c20)}
.attorneys h2{position:absolute;right:535px;top:1900px;font-size:40px;color:var(--white);text-align:right}
.attorneys .rule{left:594px;top:1964px;width:71px;background:var(--accent)}
.attorney-name{right:535px;top:2015px;font-family:"Oswald",sans-serif;font-weight:600;font-size:17px;color:var(--ink)}
.attorneys p{position:absolute;right:535px;width:520px;text-align:right;font-size:11.5px;line-height:19.5px;color:#fbeee4}
.dot{position:absolute;left:75px;width:11px;height:11px;border-radius:50%;border:1px solid #e9cdb9}
.dot.on::after{content:"";position:absolute;left:2px;top:2px;width:5px;height:5px;border-radius:50%;background:#e9cdb9}

/* blog */
.post{position:absolute;top:2469px;width:427px;height:335px;background:var(--panel)}
.post .thumb{position:absolute;left:0;top:0;width:427px;height:149px}
.post h3{position:absolute;left:12px;top:160px;font-size:15px;font-weight:500}
.post p{position:absolute;left:12px;top:186px;width:400px;font-size:11.5px;line-height:19.5px}
.post .btn{left:12px;top:281px;width:90px;height:36px;font-size:13px}

/* contact */
.field{position:absolute;border:1px solid var(--line);border-radius:4px;font-size:11px;color:#777;padding:12px 16px;background:var(--white)}
.field.focus{border-color:var(--brand-light);color:var(--brand-light)}
.contact .btn{left:552px;top:3178px;width:96px;height:35px;font-size:13px}

/* map + info */
.map{left:0;top:3283px;width:1200px;height:264px;background:linear-gradient(135deg,#9a9ea4,#80858b 60%,#8c9096)}
.info-card{left:191px;top:3301px;width:224px;height:187px;background:var(--white)}
.info-head{position:absolute;left:0;top:0;width:224px;height:38px;background:var(--brand);color:var(--white);font-family:"Oswald",sans-serif;font-weight:500;font-size:16px;display:flex;align-items:center;justify-content:center}
.info-row{position:absolute;left:15px;display:flex;gap:14px;font-size:11.5px;line-height:15px;color:#222}
.info-row svg{flex:none}

/* footer */
.footer{left:0;top:3547px;width:1200px;height:42px;background:var(--brand);color:#fbe9dc;font-size:11.5px;display:flex;align-items:center;justify-content:center}
</style>
</head>
<body>

<header>
  <div class="abs topbar"></div>
  <div class="abs brand-name">Meridian Crest Legal Group</div>
  <div class="abs call-label">Call Us On</div>
  <div class="abs call-icon">
    <svg width="16" height="16" viewBox="0 0 24 24"><path fill="#fff" d="M6.6 10.8a15.1 15.1 0 0 0 6.6 6.6l2.2-2.2c.3-.3.7-.4 1-.2 1.1.4 2.3.6 3.6.6.6 0 1 .4 1 1V20c0 .6-.4 1-1 1A17 17 0 0 1 3 4c0-.6.4-1 1-1h3.5c.6 0 1 .4 1 1 0 1.3.2 2.5.6 3.6.1.3 0 .7-.2 1z"/></svg>
  </div>
  <div class="abs call-number">+1.808.555.0142</div>

  <nav class="abs nav">
    <ul>
      <li>HOME</li><li>ABOUT US</li><li class="active">PRACTICE AREAS</li><li>ATTORNEYS</li><li>BLOG</li><li>CONTACT US</li>
    </ul>
  </nav>
  <svg class="abs search" width="20" height="20" viewBox="0 0 20 20"><circle cx="8" cy="8" r="5.5" fill="none" stroke="#8b3508" stroke-width="2.4"/><path d="M12 12l5 5" stroke="#8b3508" stroke-width="2.8" stroke-linecap="round"/></svg>
</header>

<section class="hero">
  <svg class="abs hero-bg" width="1200" height="700" viewBox="0 97 1200 700">
    <polygon points="0,97 1200,97 1200,550 753,550 443,836 188,697 0,792" fill="#8b3508"/>
    <polygon points="188,697 443,836 443,760 300,697" fill="#f5ece6" opacity=".35" transform="translate(0,0)"/>
  </svg>
  <div class="abs hero-tag">Dedicated to making sure you receive the care and attention you need</div>
  <h1>Personal Injury<br>Family &amp; Divorce<br>Child Custody</h1>
  <a class="btn">Join Us Now</a>
  <div class="photo hero-photo-a" role="img" aria-label="Attorney in a robe writing at a desk in a law library"></div>
  <div class="photo hero-photo-b" role="img" aria-label="Judge's gavel, open book and scales of justice"></div>
</section>

<section class="welcome">
  <div class="photo welcome-photo" role="img" aria-label="Group of attorneys standing at a podium in a courthouse hall"></div>
  <h2>Welcome To Meridian Crest Legal Group</h2>
  <div class="rule"></div>
  <p style="top:1021px">The experienced attorneys in the Meridian Crest Legal Group's Kailua Kona, Hawaii office provide clients with a wide range of litigation expertise, including legal claims involving divorce &amp; family, personal injury, toxic exposures, intellectual property, and real estate.</p>
  <p style="top:1100px">Our Kona office also offers commercial and hospitality litigation expertise on behalf of a wide variety of clients, including restaurants, hotels, property owners, and many others. We never wish to see our clients go to court, though if there is no other option, you're in safe hands with our seasoned trial lawyers and the many years of courtroom experience behind them.</p>
  <a class="btn">Learn More</a>
</section>

<section class="practice">
  <h2 class="section-title" style="top:1370px">Our Area Of Practice</h2>
  <div class="rule" style="left:564px;top:1431px;width:72px"></div>

  <article class="card" style="left:162px">
    <svg width="56" height="52" viewBox="0 0 56 52" fill="none" stroke="#8b3508" stroke-width="1.8"><path d="M28 4v42M14 10h28M14 10l-7 16h14zM42 10l-7 16h14z"/><path d="M20 46h16"/></svg>
    <h3>Family &amp; Divorce</h3>
    <p>Our lawyers handle all aspects of family law on the Big Island and neighboring islands...</p>
    <span class="more">Learn More <svg width="12" height="10" viewBox="0 0 12 10" fill="none" stroke="#bb6310" stroke-width="1.4"><path d="M1 1l4 4-4 4M6 1l4 4-4 4"/></svg></span>
  </article>

  <article class="card" style="left:387px">
    <svg width="56" height="52" viewBox="0 0 56 52" fill="none" stroke="#8b3508" stroke-width="1.8"><circle cx="34" cy="8" r="4"/><path d="M32 14l-6 14 8 8-4 12M26 28l-12 6M30 18l10 6M10 48h34"/></svg>
    <h3>Personal Injury</h3>
    <p>Dealing with personal injury and wrongful death claims is hard enough,...</p>
    <span class="more">Learn More <svg width="12" height="10" viewBox="0 0 12 10" fill="none" stroke="#bb6310" stroke-width="1.4"><path d="M1 1l4 4-4 4M6 1l4 4-4 4"/></svg></span>
  </article>

  <article class="card" style="left:611px">
    <svg width="60" height="52" viewBox="0 0 60 52" fill="none" stroke="#8b3508" stroke-width="1.8"><circle cx="12" cy="8" r="4"/><circle cx="30" cy="8" r="4"/><circle cx="48" cy="8" r="4"/><path d="M4 22h52M8 22v26M22 22v26M38 22v26M52 22v26M4 48h52"/></svg>
    <h3>Corporate &amp; IP</h3>
    <p>The attorneys at MCLG have been helping Big Island business owners with all their legal needs...</p>
    <span class="more">Learn More <svg width="12" height="10" viewBox="0 0 12 10" fill="none" stroke="#bb6310" stroke-width="1.4"><path d="M1 1l4 4-4 4M6 1l4 4-4 4"/></svg></span>
  </article>

  <article class="card" style="left:835px">
    <svg width="56" height="52" viewBox="0 0 56 52" fill="none" stroke="#8b3508" stroke-width="1.8"><path d="M4 18L28 4l24 14zM8 18v26M48 18v26M4 48h48M20 44V28h16v16"/></svg>
    <h3>Real Estate</h3>
    <p>Our lawyers work with home owners, buyers and property developers to ensure...</p>
    <span class="more">Learn More <svg width="12" height="10" viewBox="0 0 12 10" fill="none" stroke="#bb6310" stroke-width="1.4"><path d="M1 1l4 4-4 4M6 1l4 4-4 4"/></svg></span>
  </article>
</section>

<section class="attorneys">
  <div class="abs attorneys-band"></div>
  <div class="photo attorney-photo" role="img" aria-label="Attorney in a suit looking at a phone beside a laptop"></div>
  <h2>View Our Attorneys</h2>
  <div class="rule"></div>
  <span class="dot" style="top:2016px"></span>
  <span class="dot on" style="top:2047px"></span>
  <span class="dot" style="top:2077px"></span>
  <div class="abs attorney-name">DANIEL OKAMURA, ESQ.</div>
  <p style="top:2045px">The experienced attorneys in the Meridian Crest Legal Group's Kailua Kona, Hawaii office provide clients with a wide range of litigation expertise, including legal claims involving divorce &amp; family, personal injury, toxic exposures, intellectual property, and real estate.</p>
  <p style="top:2123px">Our Kona office also offers commercial and hospitality litigation expertise on behalf of a wide variety of clients, including restaurants, hotels, property owners, and many others. We never wish to see our clients go to court, though if there is no other option, you're in safe hands with our seasoned trial lawyers and the many years of courtroom experience behind them.</p>
</section>

<section class="blog">
  <h2 class="section-title" style="top:2351px">Personal Blog</h2>
  <div class="rule" style="left:564px;top:2415px;width:72px"></div>

  <article class="post" style="left:162px">
    <div class="thumb" role="img" aria-label="Woman reading documents in a law library" style="background:linear-gradient(90deg,#6a3a22,#3a2418 55%,#7a4a2c)"></div>
    <h3>Top 10 Things to Do Before Filing for Divorce</h3>
    <p>No one gets married with the intention of things not working out, but it's an unfortunate fact that many marriages don't work out in the end. For those in troubled marriage, here are the Top 10 things you should do before filing for a divorce...</p>
    <a class="btn">Learn More</a>
  </article>

  <article class="post" style="left:612px">
    <div class="thumb" role="img" aria-label="Speaker at a podium in a crowded hall" style="background:linear-gradient(90deg,#5a4634,#8a6a4c 50%,#3e3026)"></div>
    <h3>Top 15 Things to Do During Custody Battle</h3>
    <p>It's already tragic enough when two people who planned on spending their lives together no longer wish to see that dream through, but to compound the tragedy is when children [and their custody] get caught in the crossfire. With that in mind, here...</p>
    <a class="btn">Learn More</a>
  </article>
</section>

<section class="contact">
  <h2 class="section-title" style="top:2877px">Contact Us</h2>
  <div class="rule" style="left:564px;top:2940px;width:72px"></div>
  <div class="field" style="left:162px;top:2995px;width:280px;height:45px">Name:</div>
  <div class="field focus" style="left:460px;top:2995px;width:280px;height:45px">Email:</div>
  <div class="field" style="left:757px;top:2995px;width:281px;height:45px">Phone:</div>
  <div class="field" style="left:162px;top:3055px;width:876px;height:89px">Message:</div>
  <a class="btn">Send Message</a>
</section>

<section class="location">
  <div class="abs map" role="img" aria-label="Street map of Kailua Kona around the office"></div>
  <div class="abs info-card">
    <div class="info-head">Contact Info</div>
    <div class="info-row" style="top:52px">
    <svg width="18" height="16" viewBox="0 0 24 24"><path fill="#bb6310" d="M6.6 10.8a15.1 15.1 0 0 0 6.6 6.6l2.2-2.2c.3-.3.7-.4 1-.2 1.1.4 2.3.6 3.6.6.6 0 1 .4 1 1V20c0 .6-.4 1-1 1A17 17 0 0 1 3 4c0-.6.4-1 1-1h3.5c.6 0 1 .4 1 1 0 1.3.2 2.5.6 3.6.1.3 0 .7-.2 1z"/></svg>
    <span>+1.808.555.0142</span></div>
    <div class="info-row" style="top:81px">
    <svg width="18" height="14" viewBox="0 0 18 14" fill="none" stroke="#bb6310" stroke-width="1.6"><rect x="1" y="1" width="16" height="12"/><path d="M1 1l8 7 8-7"/></svg>
    <span>clients@tarnadvocate.example</span></div>
    <div class="info-row" style="top:110px">
    <svg width="18" height="20" viewBox="0 0 18 22"><path fill="#bb6310" d="M9 0a8 8 0 0 0-8 8c0 6 8 14 8 14s8-8 8-14a8 8 0 0 0-8-8zm0 11a3 3 0 1 1 0-6 3 3 0 0 1 0 6z"/></svg>
    <span>12-340 Lanakila Avenue,<br>Suite 210, Kailua Kona, Hawaii<br>96740.</span></div>
  </div>
</section>

<footer class="abs footer">Copyrights 2019 © Meridian Crest Legal Group. All Rights Reserved. Terms &amp; Conditions | Privacy Policy</footer>

</body>
</html>
```